I will ask the design of the business card

We are looking for business card design of the new company "R DOVE PAYGRID WORKS LLC." Based in Azerbaijan.
In case
We are working on Azerbaijan to set up the first exchange of crypto currencies.

The key currency used in exchanges is called "PLUME".
In case
We are doing project to make crypto currency infrastructure.

We provide state-of-the-art technology to the world.

```html
<!DOCTYPE html>
<html lang="en">
<head>
<meta charset="utf-8">
<title>R Dove Paygrid Works LLC – Business Card</title>
<link rel="stylesheet" href="https://fonts.googleapis.com/css2?family=Open+Sans:wght@400;700&family=Arimo:wght@400&display=swap">
<style>
  :root {
    --navy: #073a63;
    --green: #86a83a;
    --paper: #f3f3f2;
    --backdrop: #e4e4e2;
    --white: #ffffff;
  }
  * { box-sizing: border-box; margin: 0; padding: 0; }
  html, body {
    width: 1200px; height: 900px; overflow: hidden;
    background: var(--backdrop);
  }
  .card {
    position: absolute; left: 150px; top: 171px;
    width: 900px; height: 557px;
    display: flex;
    box-shadow: 0 6px 24px rgba(0,0,0,0.12);
  }
  .card__contact {
    width: 420px; height: 100%;
    background: var(--navy); color: var(--white);
    position: relative;
    font-family: "Arimo", Arial, sans-serif;
  }
  .card__divider { width: 11px; height: 100%; background: var(--green); }
  .card__brand {
    flex: 1; height: 100%; background: var(--paper);
    display: flex; align-items: center; justify-content: center;
  }
  .person {
    position: absolute; right: 31px; top: 82px; text-align: right;
  }
  .person__name {
    font-family: "Open Sans", Arial, sans-serif;
    font-weight: 700; font-size: 31px; letter-spacing: 0.3px; line-height: 1.1;
  }
  .person__role { font-size: 22px; line-height: 1.25; }
  .contact-list {
    position: absolute; right: 31px; top: 255px;
    list-style: none; text-align: right; font-size: 23px; line-height: 33px;
  }
  .contact-list li { display: flex; justify-content: flex-end; align-items: center; gap: 6px; }
  .contact-list svg { width: 20px; height: 20px; fill: var(--white); }
  .address {
    position: absolute; right: 31px; top: 408px;
    text-align: right; font-size: 23px; line-height: 32px; font-style: normal;
  }
  .brand-name {
    display: flex; align-items: center; gap: 18px;
  }
  .brand-name__mark { width: 22px; height: 22px; background: var(--green); }
  .brand-name__text {
    font-family: "Open Sans", Arial, sans-serif; font-weight: 700;
    color: var(--navy); font-size: 42px; line-height: 1.1; letter-spacing: 0.5px;
  }
</style>
</head>
<body>
  <section class="card" aria-label="Business card">
    <div class="card__contact">
      <header class="person">
        <h1 class="person__name">ELVIN KARIMOV</h1>
        <p class="person__role">Managing Director</p>
      </header>
      <ul class="contact-list">
        <li>012-480 275 316
          <svg viewBox="0 0 20 20" aria-hidden="true"><path d="M2 7c0-2 3-4 8-4s8 2 8 4v1h-4V6.5c-1-.5-2.5-.8-4-.8s-3 .3-4 .8V8H2zM5 9h10l2 7H3z"/></svg>
        </li>
        <li>012-480 275 316
          <svg viewBox="0 0 20 20" aria-hidden="true"><path d="M6 1h8a1 1 0 0 1 1 1v16a1 1 0 0 1-1 1H6a1 1 0 0 1-1-1V2a1 1 0 0 1 1-1zm1 2v11h6V3zm3 12.5a1 1 0 1 0 0 2 1 1 0 0 0 0-2z"/></svg>
        </li>
        <li>hello@paygridworks.az
          <svg viewBox="0 0 20 20" aria-hidden="true"><path d="M2 4h16v12H2zm1.5 1.5v.4L10 11l6.5-5.1v-.4zm0 2.3v6.7h13V7.8L10 13z"/></svg>
        </li>
        <li>www.paygridworks.az
          <svg viewBox="0 0 20 20" aria-hidden="true"><circle cx="10" cy="10" r="8"/><path d="M6 6c2 0 3 1 2.5 2.5S6 10 7 12s-1 3-1 3M13 4c-1 2 1 3 2 3M12 12c1 1 2 3 1 4" stroke="#073a63" stroke-width="1.6" fill="none"/></svg>
        </li>
      </ul>
      <address class="address">12345, Address Goes Here<br>Country Name, 123456</address>
    </div>
    <div class="card__divider"></div>
    <div class="card__brand">
      <div class="brand-name">
        <span class="brand-name__mark" aria-hidden="true"></span>
        <p class="brand-name__text">R DOVE<br>PAYGRID WORKS<br>LLC.</p>
      </div>
    </div>
  </section>
</body>
</html>
```